Assessment Flyer

We are looking for a marketing flyer for our business. We are a psychology practice that has recently expanded our assessment team and availability. We need a flyer to fax to GP's and other referrers. We have previously sent out rather basic flyers as it was more of a courtesy update about our practice rather than a marketing tool. We have recently created a brochure just focusing on assessments which can be used as a guide for the flyer. We want to update them about our expansion, highlight the assessments we do, introduce our new psychologists, and touch on availability.

```html
<!DOCTYPE html>
<html lang="en">
<head>
<meta charset="utf-8">
<title>Assessment Service Flyer</title>
<link rel="stylesheet" href="https://fonts.googleapis.com/css2?family=Bebas+Neue&family=Crimson+Pro:wght@600;700&family=Poppins:wght@300;400;500;600;700;800&display=swap">
<style>
  :root {
    --teal: #1aae97;
    --teal-deep: #13957f;
    --teal-dark: #0f5a52;
    --lime: #b6f22c;
    --green: #7cc243;
    --ring: #cfe8c4;
    --blush: #e9d6db;
    --ink: #1d1d1d;
    --white: #ffffff;
    --page: #f1f2f3;
  }
  * { margin: 0; padding: 0; box-sizing: border-box; }
  html, body { width: 1200px; height: 2540px; overflow: hidden; background: var(--page); }
  body { position: relative; font-family: "Poppins", sans-serif; color: var(--ink); }

  .flyer {
    position: absolute; left: 40px; top: 477px;
    width: 975px; height: 1380px;
    background: var(--white);
    transform: scale(1.1487); transform-origin: top left;
    box-shadow: 0 10px 30px rgba(0,0,0,.12);
    overflow: hidden;
  }
  .abs { position: absolute; }

  .top-band { left: 0; top: 0; width: 975px; height: 44px; background: var(--blush); }
  .hero-photo {
    left: 578px; top: 0; width: 397px; height: 623px;
    background: linear-gradient(180deg, #ddd0d4 0%, #8c8f88 28%, #5f6b55 55%, #4d5a44 80%, #6b7560 100%);
  }
  .intro-panel {
    left: 0; top: 44px; width: 578px; height: 636px;
    background: linear-gradient(180deg, var(--teal) 0%, var(--teal-deep) 100%);
  }

  .brand { left: 45px; top: 82px; display: flex; align-items: center; gap: 18px; }
  .brand-mark { width: 78px; height: 78px; border-radius: 50%; background: var(--white); flex: none; }
  .brand-name { font-weight: 500; font-size: 34px; line-height: 1.05; color: var(--white); }

  .title-top {
    left: 40px; top: 196px;
    font-family: "Bebas Neue", sans-serif; font-size: 122px; line-height: 1;
    color: var(--lime); letter-spacing: -1px;
    transform: scaleY(1.1); transform-origin: top left;
  }
  .title-bottom {
    left: 40px; top: 292px;
    font-weight: 800; font-size: 112px; line-height: 1.1;
    color: var(--white); letter-spacing: -3px;
  }
  .title-rule { left: 42px; top: 438px; width: 40px; height: 9px; background: var(--lime); }
  .intro-text {
    left: 42px; top: 468px; width: 515px;
    font-weight: 300; font-size: 21.5px; line-height: 26.5px; color: var(--white);
  }

  .availability {
    left: 578px; top: 588px; width: 357px; height: 332px;
    background: var(--green); text-align: center; color: var(--white);
  }
  .availability h2 { margin-top: 18px; font-weight: 700; font-size: 47px; line-height: 1.1; color: var(--teal-dark); }
  .availability .rule { width: 38px; height: 6px; background: var(--ink); margin: 6px auto 16px; }
  .availability .lead { font-weight: 400; font-size: 33px; line-height: 30px; }
  .availability .month { font-weight: 700; font-size: 36px; line-height: 1.2; color: var(--ink); margin-top: 4px; }
  .availability .year { font-weight: 800; font-size: 104px; line-height: 1; color: var(--teal-dark); letter-spacing: -2px; }

  .section-title {
    font-family: "Crimson Pro", serif; font-weight: 700;
    font-size: 35px; line-height: 1; color: var(--teal);
  }
  .assessments-title { left: 40px; top: 690px; }

  .assessment { text-align: center; font-size: 23.5px; line-height: 27px; color: var(--ink); }
  .assessment strong { color: var(--teal); font-weight: 600; }
  .assessment-icon {
    display: block; width: 54px; height: 54px; margin: 0 auto 10px;
    border-radius: 50%; background: var(--teal); border: 4px solid var(--ring);
  }
  .divider-v { width: 0; border-left: 2px dashed #333; }

  .team-band {
    left: 470px; top: 962px; width: 465px; height: 50px;
    background: var(--teal);
    clip-path: polygon(22px 0, 100% 0, 100% 100%, 0 100%);
    color: var(--white); text-align: center; padding-left: 16px;
    font-family: "Crimson Pro", serif; font-weight: 700; font-size: 35px; line-height: 50px;
  }
  .team-line { left: 42px; top: 1010px; width: 430px; height: 2px; background: var(--teal); }

  .member { display: flex; align-items: center; gap: 14px; }
  .member-photo {
    width: 86px; height: 86px; border-radius: 50%; flex: none;
    border: 6px solid var(--ring);
    background: linear-gradient(160deg, #c9b6a8 0%, #8b6d5c 60%, #5b4a40 100%);
  }
  .member-text { font-size: 13.5px; line-height: 15.5px; color: var(--ink); }
  .member-text b { font-weight: 600; display: block; }

  .contact { display: flex; align-items: center; gap: 8px; white-space: nowrap; }
  .phone-number { font-size: 25px; line-height: 1; color: var(--ink); letter-spacing: -0.3px; }
  .phone-number.bold { font-weight: 700; }
  .address { font-size: 15.5px; line-height: 18px; color: var(--ink); }

  .footer-band {
    left: 42px; top: 1318px; width: 893px; height: 36px;
    background: var(--teal); color: var(--white);
    display: flex; align-items: center; font-size: 16.5px;
  }
  .footer-item { display: flex; align-items: center; gap: 10px; padding-left: 8px; }
  .footer-sep { width: 2px; height: 22px; background: var(--lime); margin: 0 20px 0 42px; }
</style>
</head>
<body>
<main class="flyer">
  <div class="abs top-band"></div>
  <div class="abs hero-photo" role="img" aria-label="Photo of a woman leaping joyfully in the air above a misty mountain valley"></div>
  <section class="abs intro-panel"></section>

  <div class="abs brand">
    <span class="brand-mark"></span>
    <span class="brand-name">Northbay Psychology<br>&amp; Wellness</span>
  </div>

  <h1>
    <span class="abs title-top">ASSESSMENT</span>
    <span class="abs title-bottom">SERVICE</span>
  </h1>
  <div class="abs title-rule"></div>
  <p class="abs intro-text">Northbay Psychology and Wellness is excited to announce the expansion of our assessment team. As the need for assessment services has grown, we have worked diligently to expand our team with highly skilled psychologists to support these needs.</p>

  <aside class="abs availability">
    <h2>Availability</h2>
    <div class="rule"></div>
    <p class="lead">Appointments<br>available from</p>
    <p class="month">EARLY MARCH</p>
    <p class="year">2024</p>
  </aside>

  <h3 class="abs section-title assessments-title">Available Assessments</h3>

  <div class="abs assessment" style="left:40px;top:740px;width:145px;">
    <svg class="assessment-icon" viewBox="0 0 54 54"><rect x="16" y="14" width="16" height="20" fill="#fff"/><rect x="34" y="18" width="4" height="16" fill="#fff"/></svg>
    Educational Assessment
  </div>
  <div class="abs divider-v" style="left:199px;top:740px;height:110px;"></div>
  <div class="abs assessment" style="left:210px;top:740px;width:145px;">
    <svg class="assessment-icon" viewBox="0 0 54 54"><circle cx="23" cy="23" r="10" fill="none" stroke="#fff" stroke-width="4"/><circle cx="23" cy="23" r="3" fill="#fff"/></svg>
    Intellectual Disability
  </div>
  <div class="abs divider-v" style="left:369px;top:740px;height:110px;"></div>
  <div class="abs assessment" style="left:380px;top:740px;width:145px;">
    <svg class="assessment-icon" viewBox="0 0 54 54"><path d="M23 30 l-8 -8 a5 5 0 0 1 8 -6 a5 5 0 0 1 8 6 z" fill="#fff"/></svg>
    <span style="display:block;margin-top:6px;">Giftedness</span>
  </div>

  <div class="abs assessment" style="left:40px;top:873px;width:185px;">
    <svg class="assessment-icon" viewBox="0 0 54 54"><circle cx="23" cy="14" r="4" fill="#fff"/><rect x="20" y="19" width="6" height="18" rx="2" fill="#fff"/></svg>
    <strong>ADHD:</strong> Children and Adults
  </div>
  <div class="abs divider-v" style="left:239px;top:875px;height:110px;"></div>
  <div class="abs assessment" style="left:255px;top:873px;width:200px;">
    <svg class="assessment-icon" viewBox="0 0 54 54"><path d="M14 14 L32 32 M32 14 L14 32" stroke="#fff" stroke-width="5" stroke-linecap="round"/></svg>
    <strong>Autism:</strong> Children and Adults
  </div>

  <div class="abs team-line"></div>
  <h3 class="abs team-band">Meet the Assessment Team</h3>

  <div class="abs member" style="left:42px;top:1025px;">
    <span class="member-photo" role="img" aria-label="Portrait of Dr Maren Holt"></span>
    <span class="member-text"><b>Dr Maren Holt</b>Clinical Director</span>
  </div>
  <div class="abs member" style="left:262px;top:1025px;">
    <span class="member-photo" role="img" aria-label="Portrait of Dr Elise Warren"></span>
    <span class="member-text"><b>Dr Elise Warren</b>Registered<br>Psychologist</span>
  </div>
  <div class="abs member" style="left:500px;top:1025px;">
    <span class="member-photo" role="img" aria-label="Portrait of Dr Greta Lindqvist"></span>
    <span class="member-text"><b>Dr Greta Lindqvist</b>Counselling<br>Psychologist</span>
  </div>
  <div class="abs member" style="left:730px;top:1025px;">
    <span class="member-photo" role="img" aria-label="Portrait of Nadia Fiorelli"></span>
    <span class="member-text"><b>Nadia Fiorelli</b>Registered<br>Psychologist</span>
  </div>

  <div class="abs member" style="left:42px;top:1135px;">
    <span class="member-photo" role="img" aria-label="Portrait of Clara Benedetti"></span>
    <span class="member-text"><b>Clara<br>Benedetti</b>Registered<br>Psychologist</span>
  </div>
  <div class="abs member" style="left:262px;top:1135px;">
    <span class="member-photo" role="img" aria-label="Portrait of Rosa Delgado Whitman"></span>
    <span class="member-text"><b>Rosa<br>Delgado Whitman</b>Registered<br>Psychologist</span>
  </div>
  <div class="abs member" style="left:500px;top:1135px;">
    <span class="member-photo" role="img" aria-label="Portrait of Hannah Prescott"></span>
    <span class="member-text"><b>Hannah Prescott</b>Provisional<br>Psychologist</span>
  </div>
  <div class="abs member" style="left:730px;top:1135px;">
    <span class="member-photo" role="img" aria-label="Portrait of Joanna Keller"></span>
    <span class="member-text"><b>Joanna Keller</b>Provisional<br>Psychologist</span>
  </div>

  <div class="abs contact" style="left:42px;top:1268px;">
    <svg width="26" height="26" viewBox="0 0 26 26"><circle cx="13" cy="13" r="13" fill="var(--teal)"/><path d="M9 7 l3 3 -2 2 a8 8 0 0 0 4 4 l2 -2 3 3 -2 2 c-5 0 -10 -5 -10 -10 z" fill="#fff"/></svg>
    <span class="phone-number bold">08 7000 1234</span>
  </div>
  <div class="abs contact" style="left:262px;top:1268px;">
    <svg width="26" height="26" viewBox="0 0 26 26"><circle cx="13" cy="13" r="13" fill="var(--teal)"/><rect x="7" y="10" width="12" height="8" rx="1" fill="#fff"/><rect x="9" y="6" width="8" height="5" fill="#fff"/></svg>
    <span class="phone-number">08 6000 5678</span>
  </div>
  <div class="abs contact" style="left:500px;top:1262px;align-items:flex-start;">
    <svg width="18" height="22" viewBox="0 0 18 22"><path d="M9 1 a8 8 0 0 1 8 8 c0 5 -8 12 -8 12 s-8 -7 -8 -12 a8 8 0 0 1 8 -8z" fill="var(--teal)"/><circle cx="9" cy="9" r="3" fill="#fff"/></svg>
    <span class="address">14 Harbour Road<br>Seacliff Bay, SA 5099</span>
  </div>
  <div class="abs contact" style="left:742px;top:1262px;align-items:flex-start;">
    <svg width="18" height="22" viewBox="0 0 18 22"><path d="M9 1 a8 8 0 0 1 8 8 c0 5 -8 12 -8 12 s-8 -7 -8 -12 a8 8 0 0 1 8 -8z" fill="var(--teal)"/><circle cx="9" cy="9" r="3" fill="#fff"/></svg>
    <span class="address">3/21 Marina Terrace<br>Seacliff Bay, SA 5099</span>
  </div>

  <footer class="abs footer-band">
    <span class="footer-item">
      <svg width="22" height="22" viewBox="0 0 22 22"><circle cx="11" cy="11" r="11" fill="var(--lime)"/><rect x="5" y="7" width="12" height="8" fill="#fff"/><path d="M5 7 l6 5 6 -5" stroke="var(--teal)" fill="none" stroke-width="1.4"/></svg>
      reception@northbaypsychology.com.au
    </span>
    <span class="footer-sep"></span>
    <span class="footer-item">
      <svg width="22" height="22" viewBox="0 0 22 22"><circle cx="11" cy="11" r="11" fill="var(--lime)"/><circle cx="11" cy="11" r="6" fill="none" stroke="#fff" stroke-width="1.6"/><path d="M5 11 h12 M11 5 c-3 3 -3 9 0 12 c3 -3 3 -9 0 -12" stroke="#fff" fill="none" stroke-width="1.4"/></svg>
      www.northbaypsychology.com.au
    </span>
  </footer>
</main>
</body>
</html>
```